Stationery & Envelope Design

Executive Style looking stationery & envelope design.
Business Information:
Harlow Crest Properties
518 Meadowlark Drive, Fairhaven, OR 97321-0458
Phone: 541.555.0142
Fax: 541.555.0187

Industry/Entity Type

Business

```html
<!DOCTYPE html>
<html lang="en">
<head>
<meta charset="utf-8">
<title>Harlow Crest Properties – Stationery</title>
<link rel="stylesheet" href="https://fonts.googleapis.com/css2?family=Arimo:wght@400;600;700&display=swap">
<style>
  :root {
    --backdrop: #b08a62;
    --paper: #ffffff;
    --brand-blue: #0d55a0;
    --brand-green: #76923a;
    --ink: #222222;
    --rule: #3a3a3a;
    --muted: #555555;
    --flap-line: #b9b9b9;
    --chip-light: #f2f2f2;
    --chip-dark: #c9c9c9;
    --ghost: #dfe4ea;
  }
  * { box-sizing: border-box; margin: 0; padding: 0; }
  html, body { width: 1200px; height: 1081px; overflow: hidden; }
  body {
    background: var(--backdrop);
    font-family: "Arimo", Arial, sans-serif;
    color: var(--ink);
    position: relative;
  }

  /* ---------- Fax sheets ---------- */
  .fax-sheet {
    position: absolute;
    top: 38px;
    width: 467px;
    height: 605px;
    background: var(--paper);
    box-shadow: 0 1px 3px rgba(0,0,0,.35);
    overflow: hidden;
  }
  .fax-sheet--a { left: 90px; }
  .fax-sheet--b { left: 627px; }

  .corner-swoosh { position: absolute; left: 0; top: 0; width: 110px; height: 66px; }

  .brand-name {
    position: absolute;
    font-weight: 600;
    letter-spacing: .2px;
    white-space: nowrap;
    color: var(--brand-blue);
  }
  .fax-sheet .brand-name { left: 35px; top: 63px; font-size: 14.5px; }

  .contact-chip {
    position: absolute;
    left: 349px;
    top: 20px;
    width: 118px;
    height: 57px;
    border-radius: 6px 0 0 6px;
    background: linear-gradient(90deg, var(--chip-light), var(--chip-dark));
    padding: 5px 0 0 8px;
    font-size: 8.2px;
    line-height: 12px;
    color: #333;
  }
  .contact-chip .row { display: flex; align-items: center; gap: 3px; white-space: nowrap; }
  .contact-chip svg { width: 7px; height: 7px; flex: none; }

  .fax-title {
    position: absolute;
    left: 35px;
    top: 126px;
    font-size: 42px;
    font-weight: 400;
    letter-spacing: 1px;
  }
  .fax-fields { position: absolute; left: 139px; top: 143px; width: 305px; list-style: none; }
  .fax-fields li {
    display: flex;
    align-items: flex-end;
    height: 21.4px;
    font-size: 10.5px;
  }
  .fax-fields .label { width: 37px; }
  .fax-fields .line { flex: 1; border-bottom: 1px solid var(--rule); margin-bottom: 4px; }

  .ghost-name {
    position: absolute;
    right: 14px;
    bottom: 36px;
    font-size: 12px;
    font-weight: 600;
    color: var(--ghost);
    white-space: nowrap;
  }

  /* ---------- Envelopes ---------- */
  .envelope {
    position: absolute;
    width: 523px;
    height: 228px;
    background: var(--paper);
    box-shadow: 0 1px 3px rgba(0,0,0,.35);
    overflow: hidden;
  }
  .envelope .flap { position: absolute; left: 0; top: 0; width: 100%; height: 70px; }
  .envelope .flap svg { position: absolute; inset: 0; width: 100%; height: 100%; }
  .envelope .flap .brand-name {
    left: 50%;
    top: 29px;
    transform: translateX(-50%);
    font-size: 14px;
  }

  .envelope--back-white { left: 86px; top: 663px; }
  .envelope--back-grey  { left: 56px; top: 744px; }
  .envelope--back-grey .brand-name { color: var(--muted); }
  .envelope--back-green { left: 629px; top: 662px; }
  .envelope--back-blue  { left: 612px; top: 731px; }
  .envelope--back-green .brand-name,
  .envelope--back-blue .brand-name { color: #ffffff; }
  .envelope--back-black { left: 601px; top: 813px; }
  .envelope--back-black .brand-name { color: #111111; }

  .envelope--front { left: 51px; top: 813px; width: 522px; height: 227px; }
  .envelope--front .brand-name { left: 24px; top: 58px; font-size: 12.5px; }
  .return-address {
    position: absolute;
    left: 24px;
    top: 84px;
    font-size: 7.6px;
    color: #333;
    white-space: nowrap;
  }
  .stamp-box {
    position: absolute;
    right: 2px;
    top: 146px;
    width: 119px;
    height: 57px;
    border-radius: 7px;
    background: linear-gradient(90deg, var(--chip-light), var(--chip-dark));
  }
</style>
</head>
<body>

  <section class="fax-sheet fax-sheet--a">
    <svg class="corner-swoosh" viewBox="0 0 110 66" aria-hidden="true">
      <path d="M0 0 H58 Q18 12 0 58 Z" fill="var(--brand-blue)"/>
      <path d="M6 64 Q30 6 108 2" fill="none" stroke="var(--brand-green)" stroke-width="4"/>
    </svg>
    <div class="brand-name">HARLOW CREST PROPERTIES</div>
    <div class="contact-chip">
      <div class="row">518 Meadowlark Drive</div>
      <div class="row">Fairhaven, OR 97321-0458</div>
      <div class="row">
        <svg viewBox="0 0 10 10"><circle cx="5" cy="5" r="5" fill="var(--brand-blue)"/></svg>541.555.0142
      </div>
      <div class="row">
        <svg viewBox="0 0 10 10"><rect x="0" y="2" width="10" height="7" rx="1" fill="var(--brand-blue)"/></svg>541.555.0187
      </div>
    </div>
    <h1 class="fax-title">FAX</h1>
    <ul class="fax-fields">
      <li><span class="label">To</span><span class="line"></span></li>
      <li><span class="label">From</span><span class="line"></span></li>
      <li><span class="label">Fax</span><span class="line"></span></li>
      <li><span class="label">Pages</span><span class="line"></span></li>
      <li><span class="label">Phone</span><span class="line"></span></li>
      <li><span class="label">Re</span><span class="line"></span></li>
      <li><span class="label">Date</span><span class="line"></span></li>
    </ul>
    <div class="ghost-name">HARLOW CREST PROPERTIES</div>
  </section>

  <section class="fax-sheet fax-sheet--b">
    <svg class="corner-swoosh" viewBox="0 0 110 66" aria-hidden="true">
      <path d="M0 0 H58 Q18 12 0 58 Z" fill="var(--brand-blue)"/>
      <path d="M6 64 Q30 6 108 2" fill="none" stroke="var(--brand-green)" stroke-width="4"/>
    </svg>
    <div class="brand-name">HARLOW CREST PROPERTIES</div>
    <div class="contact-chip">
      <div class="row">
        <svg viewBox="0 0 10 10"><circle cx="5" cy="5" r="5" fill="var(--brand-blue)"/></svg>541.555.0142
      </div>
      <div class="row">
        <svg viewBox="0 0 10 10"><rect x="0" y="2" width="10" height="7" rx="1" fill="var(--brand-blue)"/></svg>541.555.0187
      </div>
      <div class="row">518 Meadowlark Drive</div>
      <div class="row">Fairhaven, OR 97321-0458</div>
    </div>
    <h1 class="fax-title">FAX</h1>
    <ul class="fax-fields">
      <li><span class="label">To</span><span class="line"></span></li>
      <li><span class="label">From</span><span class="line"></span></li>
      <li><span class="label">Fax</span><span class="line"></span></li>
      <li><span class="label">Pages</span><span class="line"></span></li>
      <li><span class="label">Phone</span><span class="line"></span></li>
      <li><span class="label">Re</span><span class="line"></span></li>
      <li><span class="label">Date</span><span class="line"></span></li>
    </ul>
    <div class="ghost-name">HARLOW CREST PROPERTIES</div>
  </section>

  <section class="envelope envelope--back-white">
    <div class="flap">
      <svg viewBox="0 0 523 70" preserveAspectRatio="none" aria-hidden="true">
        <polyline points="0,0 14,66 509,66 523,0" fill="none" stroke="var(--flap-line)" stroke-width="1"/>
      </svg>
      <div class="brand-name">HARLOW CREST PROPERTIES</div>
    </div>
  </section>

  <section class="envelope envelope--back-grey">
    <div class="flap">
      <svg viewBox="0 0 523 70" preserveAspectRatio="none" aria-hidden="true">
        <polyline points="0,0 14,66 509,66 523,0" fill="none" stroke="var(--flap-line)" stroke-width="1"/>
      </svg>
      <div class="brand-name">HARLOW CREST PROPERTIES</div>
    </div>
  </section>

  <section class="envelope envelope--back-green">
    <div class="flap">
      <svg viewBox="0 0 523 70" preserveAspectRatio="none" aria-hidden="true">
        <polygon points="0,0 523,0 509,70 14,70" fill="var(--brand-green)"/>
      </svg>
      <div class="brand-name">HARLOW CREST PROPERTIES</div>
    </div>
  </section>

  <section class="envelope envelope--back-blue">
    <div class="flap">
      <svg viewBox="0 0 523 70" preserveAspectRatio="none" aria-hidden="true">
        <polygon points="0,0 523,0 509,70 14,70" fill="var(--brand-blue)"/>
      </svg>
      <div class="brand-name">HARLOW CREST PROPERTIES</div>
    </div>
  </section>

  <section class="envelope envelope--back-black">
    <div class="flap">
      <svg viewBox="0 0 523 70" preserveAspectRatio="none" aria-hidden="true">
        <polyline points="0,0 14,66 509,66 523,0" fill="none" stroke="var(--flap-line)" stroke-width="1"/>
      </svg>
      <div class="brand-name">HARLOW CREST PROPERTIES</div>
    </div>
  </section>

  <section class="envelope envelope--front">
    <svg class="corner-swoosh" viewBox="0 0 110 66" aria-hidden="true">
      <path d="M0 0 H58 Q18 12 0 58 Z" fill="var(--brand-blue)"/>
      <path d="M6 64 Q30 6 108 2" fill="none" stroke="var(--brand-green)" stroke-width="4"/>
    </svg>
    <div class="brand-name">HARLOW CREST PROPERTIES</div>
    <div class="return-address">Harlow Crest Properties, 518 Meadowlark Drive, Fairhaven, OR 97321-0458</div>
    <div class="stamp-box"></div>
  </section>

</body>
</html>
```